Business Cards for new orthopaedic surgery practice

My husband and I are starting our own orthopaedic surgery practice. We are looking for a business card that is uniform, but one will have my name/title and the other will have his. You can just create one design with my name on it for now. But when I choose your design as the winning design I will ask that you add another copy with his name/title.

We are looking for classy, simple, elite all in one. We like dark blues/a little gold/yellow. Something that goes with our logo. We want our logo incorporated. Here is all the info you need:
Business name: RV Bone & Vitality Center
Location: 38517 North Willowmere Ave
Maple Hollow, FL 33990
Phone: 954-218-4063
Fax: 954-582-7341
Email: info@myrvbonecare.example

Names: Lydia Vance, M.D.
Board Certified Hand and Upper Extremity Surgeon

Ebo Dansu, M.D.
Board Certified Hip & Knee Replacement/General Orthopaedic Surgeon

Can decide what you want to put on the back. Maybe a slogan:
Grounded in Skill. Centered on You

I am just going to upload our logo. The only thing is if we select you as the winning design, the location, and phone numbers may change. We will need your help to update that once fully solidified.

Industry/Entity Type

Medical

Contact Information for Business Card

Colors
0054AA
0677BA
7BADD7
CADEEF
E8F1F8
0094D4
00A9DD
6FCCEA
C7EBF8
E9F6FB

Requirements
Must have
• class, appeal,
Should not have
• We want to air on the side of masculine if we are looking at masculine vs. feminine feel. But we still want it classy, sophisticated, and something we will love

```html
<!DOCTYPE html>
<html lang="en">
<head>
<meta charset="utf-8">
<title>RV Bone &amp; Vitality Center – Business Card</title>
<link rel="stylesheet" href="https://fonts.googleapis.com/css2?family=Tinos:wght@400;700&display=swap">
<style>
  :root {
    --navy: #1b2a57;
    --navy-soft: #34498a;
    --gold: #c9a24f;
    --gold-edge: #b8923f;
    --text-grey: #4a4d55;
    --white: #ffffff;
    --backdrop: #e8e8e8;
  }
  * { box-sizing: border-box; margin: 0; padding: 0; }
  html, body { width: 1200px; height: 801px; overflow: hidden; }
  body {
    background: var(--backdrop);
    font-family: "Tinos", "Times New Roman", serif;
    position: relative;
  }
  .card {
    position: absolute;
    top: 246px;
    width: 540px;
    height: 309px;
    background: var(--navy);
    border: 3px solid var(--gold-edge);
    border-radius: 3px;
    overflow: hidden;
  }
  .card--front { left: 40px; }
  .card--back { left: 620px; }

  .front-panel { position: absolute; inset: 0; width: 100%; height: 100%; }

  .brand {
    position: absolute;
    top: 30px;
    right: 28px;
    display: flex;
    align-items: center;
    gap: 10px;
  }
  .brand__dot {
    width: 16px; height: 16px;
    border-radius: 50%;
    border: 2px solid var(--gold);
  }
  .brand__name {
    color: var(--white);
    font-size: 17px;
    letter-spacing: 1.5px;
    text-transform: uppercase;
  }
  .brand-rule {
    position: absolute;
    top: 66px; right: 28px;
    width: 180px; height: 1px;
    background: var(--gold);
  }

  .contact {
    position: absolute;
    top: 130px;
    right: 28px;
    list-style: none;
    text-align: right;
    color: var(--white);
    font-size: 15px;
    line-height: 26px;
  }
  .contact li { display: flex; justify-content: flex-end; align-items: center; gap: 8px; }
  .contact svg { width: 14px; height: 14px; fill: var(--gold); }

  .person {
    position: absolute;
    left: 26px;
    top: 172px;
  }
  .person__name { color: var(--gold); font-size: 23px; font-weight: 700; }
  .person__title { color: var(--navy); font-size: 15px; line-height: 18px; margin-top: 4px; }
  .person__address { color: var(--text-grey); font-size: 14px; line-height: 18px; margin-top: 10px; }

  .back-brand {
    position: absolute;
    top: 70px; left: 0; right: 0;
    display: flex; flex-direction: column; align-items: center; gap: 14px;
  }
  .back-brand__ring {
    width: 64px; height: 64px;
    border-radius: 50%;
    border: 2px solid var(--navy-soft);
  }
  .back-brand__name {
    color: var(--navy-soft);
    font-size: 22px;
    letter-spacing: 2px;
    text-transform: uppercase;
  }
  .tagline {
    position: absolute;
    bottom: 36px; left: 0; right: 0;
    text-align: center;
    color: var(--gold);
    font-size: 17px;
    font-weight: 700;
  }
</style>
</head>
<body>
  <section class="card card--front" aria-label="Business card front">
    <svg class="front-panel" viewBox="0 0 534 303" preserveAspectRatio="none" aria-hidden="true">
      <defs>
        <linearGradient id="silverPanel" x1="0" y1="0" x2="1" y2="1">
          <stop offset="0" stop-color="#e4e6ec"/>
          <stop offset="1" stop-color="#f5f6f8"/>
        </linearGradient>
      </defs>
      <polygon points="0,110 170,110 370,303 0,303" fill="url(#silverPanel)"/>
    </svg>

    <div class="brand">
      <span class="brand__dot"></span>
      <span class="brand__name">RV Bone &amp; Vitality Center</span>
    </div>
    <div class="brand-rule"></div>

    <ul class="contact">
      <li>954-218-4063
        <svg viewBox="0 0 24 24"><path d="M6.6 10.8a15 15 0 0 0 6.6 6.6l2.2-2.2c.3-.3.7-.4 1-.2 1.1.4 2.3.6 3.6.6.6 0 1 .4 1 1V20c0 .6-.4 1-1 1A17 17 0 0 1 3 4c0-.6.4-1 1-1h3.5c.6 0 1 .4 1 1 0 1.3.2 2.5.6 3.6.1.3 0 .7-.2 1z"/></svg>
      </li>
      <li>954-582-7341
        <svg viewBox="0 0 24 24"><path d="M6 2h10v6H6zM3 9h18v10h-3v3H6v-3H3zm5 7v4h8v-4z"/></svg>
      </li>
      <li>info@myrvbonecare.example
        <svg viewBox="0 0 24 24"><path d="M2 5h20v14H2zm2 2v.5l8 5 8-5V7z"/></svg>
      </li>
    </ul>

    <div class="person">
      <h1 class="person__name">Lydia Vance, M.D.</h1>
      <p class="person__title">Board Certified Hand and<br>Upper Extremity Surgeon</p>
      <p class="person__address">38517 North Willowmere Ave<br>Maple Hollow, FL 33990</p>
    </div>
  </section>

  <section class="card card--back" aria-label="Business card back">
    <div class="back-brand">
      <span class="back-brand__ring"></span>
      <span class="back-brand__name">RV Bone &amp; Vitality Center</span>
    </div>
    <p class="tagline">Grounded in Skill. Centered on You</p>
  </section>
</body>
</html>
```